Q&J RESTORATION

I want a brochure similiar to the example i've attached.
My company name is Q&J Restoration. The website is: Q-J-Restoration.example.
The phone number is 919.555.0147.

I don't like the "yellow" being the main color of the example so I'm open to suggestions. I want something CLEAN & Simple, like our logo . This will be a bi fold brochure

```html
<!DOCTYPE html>
<html lang="en">
<head>
<meta charset="utf-8">
<title>Q&amp;J Restoration — Bi-fold Brochure</title>
<link rel="stylesheet" href="https://fonts.googleapis.com/css2?family=Poppins:wght@400;500;600;700;800&display=swap">
<style>
:root{
  --stage:#c9c9c9;
  --paper:#ece8e6;
  --ink:#111111;
  --charcoal:#2a2a2a;
  --band:#e9e7e6;
  --muted:#dcdcdc;
  --white:#ffffff;
}
*{margin:0;padding:0;box-sizing:border-box}
html,body{width:1200px;height:2547px;overflow:hidden}
body{background:var(--stage);font-family:"Poppins",sans-serif;position:relative;color:var(--ink)}
.section{position:absolute;left:0;width:1200px}
.section--front{top:0;height:840px}
.section--outer{top:840px;height:740px;background:#c4c4c4}
.section--inner{top:1580px;height:967px;background:#c1c1c1}
.page{position:absolute;width:460px;height:650px;overflow:hidden;box-shadow:0 14px 30px rgba(0,0,0,.25)}
.page svg.shapes{position:absolute;inset:0}
.cover{background:var(--paper)}
.brand-name{position:absolute;font-weight:500;font-size:22px;letter-spacing:.5px;white-space:nowrap}
.cover .brand-name{top:108px;right:48px;color:var(--ink)}
.cover__heading{position:absolute;left:86px;top:292px;color:var(--white)}
.cover__kicker{font-size:17px;font-weight:600;letter-spacing:1px}
.cover__title{font-size:38px;font-weight:800;line-height:1.02;letter-spacing:.5px}
.cover__web{position:absolute;top:560px;left:0;right:0;text-align:center;font-size:16px;font-weight:600;letter-spacing:1px}
.back{background:var(--ink)}
.back__photo{position:absolute;inset:0;background:radial-gradient(circle at 70% 25%,#3a3a3a,#121212 70%)}
.back .brand-name{top:160px;left:0;right:0;text-align:center;color:var(--white)}
.back__tagline{position:absolute;top:262px;left:0;right:0;text-align:center;font-size:17px;font-weight:700;color:var(--ink)}
.contacts{position:absolute;top:350px;left:0;right:0;list-style:none;text-align:center;color:var(--white);font-size:15px;letter-spacing:1px}
.contacts li{margin-bottom:16px}
.contacts .ico{display:block;margin:0 auto 6px}
.spread{position:absolute;left:92px;top:88px;width:1052px;height:760px;overflow:hidden;box-shadow:0 14px 30px rgba(0,0,0,.25)}
.spread__photo{position:absolute;left:0;top:0;width:526px;height:760px;background:linear-gradient(180deg,#6d6d6d 0%,#575757 55%,#8a8a8a 100%)}
.spread__photo-right{position:absolute;left:526px;top:0;width:526px;height:760px;background:linear-gradient(180deg,#5d5d5d,#8d8d8d)}
.spread svg.shapes{position:absolute;inset:0}
.info{position:absolute;left:0;top:0;width:1052px;height:760px;color:var(--white)}
.info__title{position:absolute;left:632px;top:78px;font-size:36px;font-weight:700;line-height:1.05}
.info__sub{position:absolute;left:632px;top:162px;font-size:18px;font-weight:500}
.services{position:absolute;left:560px;top:208px;display:flex;gap:28px;list-style:none;color:var(--ink);font-size:20px;font-weight:500}
.services li{display:flex;align-items:center;gap:6px}
.feature{position:absolute;width:230px}
.feature__head{display:flex;align-items:center;gap:12px;font-size:17px;font-weight:600;line-height:1.2}
.feature__icon{flex:none;width:44px;height:44px;border-radius:50%;background:var(--white);display:flex;align-items:center;justify-content:center}
.feature__text{margin:10px 0 0 56px;font-size:9.5px;line-height:1.35;color:var(--muted)}
.info__closing{position:absolute;left:546px;width:506px;top:590px;text-align:center;font-size:16px;letter-spacing:.5px}
.info .brand-name{top:640px;left:546px;width:506px;text-align:center;color:var(--white);font-size:20px}
</style>
</head>
<body>

<section class="section section--front">
  <article class="page cover" style="left:370px;top:95px">
    <svg class="shapes" width="460" height="650" viewBox="0 0 460 650" aria-hidden="true">
      <polygon points="0,0 150,0 0,300" fill="#111"/>
      <polygon points="110,250 460,250 460,440 40,440" fill="#2a2a2a"/>
    </svg>
    <p class="brand-name">Q&amp;J Restoration</p>
    <div class="cover__heading">
      <p class="cover__kicker">THREE GENERATIONS OF</p>
      <h1 class="cover__title">RESTORATION<br>EXPERIENCE</h1>
    </div>
    <p class="cover__web">www.Q-J-Restoration.example</p>
  </article>
</section>

<section class="section section--outer">
  <article class="page back" style="left:140px;top:45px">
    <div class="back__photo" role="img" aria-label="Dark toned photo of a restored home interior"></div>
    <svg class="shapes" width="460" height="650" viewBox="0 0 460 650" aria-hidden="true">
      <polygon points="0,240 460,250 460,300 0,290" fill="#e9e7e6"/>
    </svg>
    <p class="brand-name">Q&amp;J Restoration</p>
    <p class="back__tagline">Insurance Claim? We're on Your Team.</p>
    <ul class="contacts">
      <li><svg class="ico" width="22" height="22" viewBox="0 0 22 22"><circle cx="11" cy="11" r="11" fill="#fff"/><path d="M7 6l2 0 1 3-1.5 1a7 7 0 0 0 3.5 3.5l1-1.5 3 1v2a2 2 0 0 1-2 1A10 10 0 0 1 6 8a2 2 0 0 1 1-2z" fill="#111"/></svg>919.555.0147</li>
      <li><svg class="ico" width="22" height="22" viewBox="0 0 22 22"><circle cx="11" cy="11" r="11" fill="#fff"/><rect x="6" y="7.5" width="10" height="7" fill="none" stroke="#111" stroke-width="1.4"/><path d="M6 7.5l5 4 5-4" fill="none" stroke="#111" stroke-width="1.4"/></svg>info@Q-J-Restoration.example</li>
      <li><svg class="ico" width="22" height="22" viewBox="0 0 22 22"><circle cx="11" cy="11" r="11" fill="#fff"/><circle cx="11" cy="11" r="5.5" fill="none" stroke="#111" stroke-width="1.3"/><path d="M5.5 11h11M11 5.5c-3 3-3 8 0 11M11 5.5c3 3 3 8 0 11" fill="none" stroke="#111" stroke-width="1.1"/></svg>www.Q-J-Restoration.example</li>
    </ul>
  </article>
  <article class="page cover" style="left:600px;top:45px">
    <svg class="shapes" width="460" height="650" viewBox="0 0 460 650" aria-hidden="true">
      <polygon points="0,0 150,0 0,300" fill="#111"/>
      <polygon points="110,250 460,250 460,440 40,440" fill="#2a2a2a"/>
    </svg>
    <p class="brand-name">Q&amp;J Restoration</p>
    <div class="cover__heading">
      <p class="cover__kicker">THREE GENERATIONS OF</p>
      <h1 class="cover__title">RESTORATION<br>EXPERIENCE</h1>
    </div>
    <p class="cover__web">www.Q-J-Restoration.example</p>
  </article>
</section>

<section class="section section--inner">
  <div class="spread">
    <div class="spread__photo" role="img" aria-label="Photo of a happy senior couple dancing in a renovated living room"></div>
    <div class="spread__photo-right" role="img" aria-label="Continuation of the living room photo with a sofa"></div>
    <svg class="shapes" width="1052" height="760" viewBox="0 0 1052 760" aria-hidden="true">
      <polyline points="620,0 448,380 670,760" fill="none" stroke="#f2f2f2" stroke-width="5"/>
      <polygon points="640,0 1052,0 1052,760 690,760 468,380" fill="#111"/>
      <polygon points="547,198 1052,198 1052,240 528,240" fill="#e9e7e6"/>
    </svg>
    <div class="info">
      <h2 class="info__title">WATER OR<br>MOLD DAMAGE?</h2>
      <p class="info__sub">What happens after the cleanup?</p>
      <ul class="services">
        <li><svg width="14" height="14" viewBox="0 0 14 14"><circle cx="7" cy="7" r="7" fill="#111"/><path d="M3.8 7.2l2.2 2.2 4.2-4.6" fill="none" stroke="#fff" stroke-width="1.8"/></svg>BUILD</li>
        <li><svg width="14" height="14" viewBox="0 0 14 14"><circle cx="7" cy="7" r="7" fill="#111"/><path d="M3.8 7.2l2.2 2.2 4.2-4.6" fill="none" stroke="#fff" stroke-width="1.8"/></svg>RENOVATE</li>
        <li><svg width="14" height="14" viewBox="0 0 14 14"><circle cx="7" cy="7" r="7" fill="#111"/><path d="M3.8 7.2l2.2 2.2 4.2-4.6" fill="none" stroke="#fff" stroke-width="1.8"/></svg>RESTORE</li>
      </ul>
      <div class="feature" style="left:554px;top:272px">
        <div class="feature__head"><span class="feature__icon"><svg width="22" height="22" viewBox="0 0 22 22"><circle cx="9" cy="9" r="6" fill="none" stroke="#111" stroke-width="2"/><path d="M13.5 13.5l5 5" stroke="#111" stroke-width="2.4"/></svg></span>ADJUSTER'S<br>INSPECTION</div>
        <p class="feature__text">Feel Confident. Be sure you received a fair and accurate assessment &amp; repair of all damages with our team's use of industry leading Estimating.</p>
      </div>
      <div class="feature" style="left:786px;top:272px">
        <div class="feature__head"><span class="feature__icon"><svg width="22" height="22" viewBox="0 0 22 22"><circle cx="11" cy="11" r="8" fill="none" stroke="#111" stroke-width="2"/><path d="M11 6v5l3 2" fill="none" stroke="#111" stroke-width="2"/></svg></span>TIMELY<br>SETTLEMENT</div>
        <p class="feature__text">Don't wait. Minimize the hassle of long processing times from Estimate to Settlement when you team up with an Insurance Repair Specialist.</p>
      </div>
      <div class="feature" style="left:554px;top:432px">
        <div class="feature__head"><span class="feature__icon"><svg width="22" height="22" viewBox="0 0 22 22"><path d="M3 11l8-7 8 7v8H3z" fill="#111"/><rect x="9" y="13" width="4" height="6" fill="#fff"/></svg></span>UNDER ONE<br>ROOF</div>
        <p class="feature__text">Don't Worry. You won't need to arrange meetings with multiple contractors; we'll take care of everything from demo to final cleanup.</p>
      </div>
      <div class="feature" style="left:786px;top:432px">
        <div class="feature__head"><span class="feature__icon"><svg width="22" height="22" viewBox="0 0 22 22"><path d="M11 2l2.6 5.6 6 .7-4.5 4.1 1.2 6L11 15.4 5.7 18.4l1.2-6L2.4 8.3l6-.7z" fill="#111"/></svg></span>SUPERIOR<br>CRAFTSMANSHIP</div>
        <p class="feature__text">Don't settle for satisfactory. Our team is committed to the highest standards of excellence every step of the way. Trust us when we say that we'll make you smile.</p>
      </div>
      <p class="info__closing">HERE FOR YOU, EVERY STEP OF THE WAY.</p>
      <p class="brand-name">Q&amp;J Restoration</p>
    </div>
  </div>
</section>

</body>
</html>
```